Business Cards Design for the electrical wholesaler: clean bold dynamic :)

We need a business card design that would follow our latest brand guidelines. As an electrical wholesaler we want to bring a fresh look and feel into the industry. The design should be clean bold and dynamic. It should come alive with the renewed energy of our green colour. Our grey colour should keep things balanced and complement the notion of maturity and responsibility. We employ Lato as a corporate font however are not bound by this font and we’re open to interpretation here.

Target Market(s)

Electrical contractors

Industry/Entity Type

Business

Contact Information for Business Card

Logo
Name & Surname: Halyna Dorosh
Job Title: Director of Marketing
Email: halya.dorosh@quillmail.example
Cell phone: 780.555.0297
Address: 20517 - 87 Ave. Edmonton, AB, Canada. T6K 4N8
Business Phone: 780.555.0184
Website: www.brovix.example

Font styles to use
Other font styles liked:
• Lato

Requirements
Must have
• Logo & website
Nice to have
• Brand elements - some of them you may find in the attached Brand Guidelines (e.g. three lines on the background signifying "W")

```html
<!DOCTYPE html>
<html lang="en">
<head>
<meta charset="utf-8">
<title>Brovix Electrical Wholesalers – Business Card</title>
<link rel="stylesheet" href="https://fonts.googleapis.com/css2?family=Lato:wght@400;700;900&display=swap">
<style>
  :root {
    --brand-green: #8cc63f;
    --brand-grey: #4a4a4c;
    --text-grey: #5a5a5c;
    --card-dark: #1c1c1c;
    --card-light: #ffffff;
    --backdrop: #d9d9db;
  }
  * { margin: 0; padding: 0; box-sizing: border-box; }
  html, body {
    width: 1200px;
    height: 912px;
    overflow: hidden;
    background: var(--backdrop);
    font-family: "Lato", Arial, sans-serif;
  }
  .stage { position: relative; width: 1200px; height: 912px; }
  .card {
    position: absolute;
    left: 250px;
    width: 700px;
    height: 400px;
    border-radius: 22px;
    overflow: hidden;
  }
  .card--back {
    top: 40px;
    background: var(--card-dark);
    display: flex;
    align-items: center;
    justify-content: center;
  }
  .card--front {
    top: 472px;
    background: var(--card-light);
    display: flex;
    align-items: center;
    padding: 0 50px 0 60px;
  }
  .wordmark { display: flex; align-items: center; gap: 14px; }
  .wordmark__dot {
    width: 26px; height: 26px; border-radius: 50%;
    background: var(--brand-green);
  }
  .wordmark__name {
    font-weight: 900;
    font-size: 88px;
    line-height: 1;
    letter-spacing: -1px;
  }
  .card--back .wordmark__name { color: var(--card-light); }
  .brand-block {
    width: 260px;
    flex: none;
    display: flex;
    flex-direction: column;
    align-items: flex-start;
  }
  .card--front .wordmark__name { color: var(--brand-grey); font-size: 66px; }
  .card--front .wordmark__dot { width: 24px; height: 24px; }
  .brand-block__tagline {
    margin-top: 8px;
    font-weight: 700;
    font-size: 13px;
    letter-spacing: 2.4px;
    text-transform: uppercase;
    color: var(--brand-grey);
  }
  .divider {
    width: 2px;
    height: 240px;
    flex: none;
    background: var(--brand-green);
    margin: 0 30px 0 10px;
  }
  .contact { min-width: 0; }
  .contact__name { font-weight: 700; font-size: 28px; color: var(--brand-green); line-height: 1.2; }
  .contact__title { font-size: 18px; color: var(--text-grey); margin-top: 2px; }
  .contact__address { font-size: 18px; color: var(--text-grey); margin-top: 14px; line-height: 1.3; }
  .contact__list { list-style: none; margin-top: 12px; }
  .contact__item {
    display: flex;
    align-items: center;
    gap: 12px;
    font-size: 18px;
    color: var(--text-grey);
    line-height: 1.45;
    white-space: nowrap;
  }
  .contact__icon { width: 14px; height: 14px; flex: none; }
  .contact__accent { color: var(--brand-green); }
</style>
</head>
<body>
<main class="stage">
  <section class="card card--back" aria-label="Card back">
    <div class="wordmark">
      <span class="wordmark__dot"></span>
      <span class="wordmark__name">brovix</span>
    </div>
  </section>

  <section class="card card--front" aria-label="Card front">
    <div class="brand-block">
      <div class="wordmark">
        <span class="wordmark__dot"></span>
        <span class="wordmark__name">brovix</span>
      </div>
      <p class="brand-block__tagline">Electrical Wholesalers</p>
    </div>

    <div class="divider"></div>

    <div class="contact">
      <p class="contact__name">Halyna Dorosh</p>
      <p class="contact__title">Director of Marketing</p>
      <p class="contact__address">20517 87ave<br>T6K4N8 Edmonton, Alberta</p>
      <ul class="contact__list">
        <li class="contact__item">
          <svg class="contact__icon" viewBox="0 0 24 24"><path fill="#8cc63f" d="M6.6 10.8a15.1 15.1 0 0 0 6.6 6.6l2.2-2.2c.3-.3.7-.4 1-.2 1.1.4 2.3.6 3.6.6.6 0 1 .4 1 1V20c0 .6-.4 1-1 1A17 17 0 0 1 3 4c0-.6.4-1 1-1h3.5c.6 0 1 .4 1 1 0 1.3.2 2.5.6 3.6.1.3 0 .7-.2 1z"/></svg>
          780.555.0184
        </li>
        <li class="contact__item">
          <svg class="contact__icon" viewBox="0 0 24 24"><rect x="6" y="2" width="12" height="20" rx="2" fill="none" stroke="#8cc63f" stroke-width="2"/><circle cx="12" cy="18" r="1.3" fill="#8cc63f"/></svg>
          780.555.0297
        </li>
        <li class="contact__item">
          <svg class="contact__icon" viewBox="0 0 24 24"><rect x="3" y="5" width="18" height="14" rx="1.5" fill="none" stroke="#8cc63f" stroke-width="2"/><path d="M3.5 6l8.5 7 8.5-7" fill="none" stroke="#8cc63f" stroke-width="2"/></svg>
          halya.dorosh@quillmail.example
        </li>
        <li class="contact__item">
          <svg class="contact__icon" viewBox="0 0 24 24"><circle cx="12" cy="12" r="9" fill="none" stroke="#8cc63f" stroke-width="2"/><path d="M3 12h18M12 3c3 3 3 15 0 18M12 3c-3 3-3 15 0 18" fill="none" stroke="#8cc63f" stroke-width="1.6"/></svg>
          <span>www.<span class="contact__accent">brovix</span>.example</span>
        </li>
      </ul>
    </div>
  </section>
</main>
</body>
</html>
```